Need help in designing new business card utilizing our new logo.

BuildMark Solutions works with Construction Business Owners, Managers & IT Professionals to strengthen software usage and increase user productivity.

Our Construction Accounting and Mobile Field Management Software Clients engage with us in the following areas:

New Software Implementations
Software Re-Implementations
Redesigning Software Usage at the User Level
Project Coordination & Management
Continued Software Support

Old tag line:
Measuring Needs - Delivering Results

www.buildmark-solutions.example

Ridge 4 is a product, but not needed for a new business card.

```html
<!DOCTYPE html>
<html lang="en">
<head>
<meta charset="utf-8">
<title>BuildMark Solutions – Business Card</title>
<link href="https://fonts.googleapis.com/css2?family=Open+Sans:wght@400;600;700&display=swap" rel="stylesheet">
<style>
  :root {
    --brand-blue: #1c14b4;
    --band-blue: #170fa6;
    --ink: #3a3a3a;
    --rule: #c8c8c8;
    --paper: #ffffff;
    --backdrop: #8d8d8d;
  }
  * { box-sizing: border-box; margin: 0; padding: 0; }
  html, body { width: 1200px; height: 802px; overflow: hidden; }
  body {
    background: var(--backdrop);
    font-family: "Open Sans", Arial, sans-serif;
    position: relative;
  }
  .card {
    position: absolute;
    top: 274px;
    width: 443px;
    height: 265px;
    background: var(--paper);
    box-shadow: 2px 3px 6px rgba(0,0,0,0.35);
  }
  .card--front { left: 136px; }
  .card--back { left: 624px; }

  .tagline-band {
    position: absolute;
    left: 0; right: 0; bottom: 0;
    height: 39px;
    background: var(--band-blue);
    color: #fff;
    font-size: 13px;
    display: flex;
    align-items: center;
    justify-content: center;
    letter-spacing: 0.1px;
    text-transform: uppercase;
  }

  /* Front */
  .brand {
    position: absolute;
    right: 28px;
    top: 62px;
    display: flex;
    align-items: center;
    gap: 10px;
    color: var(--brand-blue);
    font-weight: 700;
    font-size: 25px;
  }
  .brand__mark {
    width: 26px; height: 26px;
    background: var(--brand-blue);
  }
  .holder {
    position: absolute;
    left: 24px;
    top: 134px;
    right: 28px;
  }
  .holder__name-row { display: flex; align-items: center; gap: 8px; }
  .holder__name {
    color: var(--brand-blue);
    font-weight: 700;
    font-size: 16.5px;
    letter-spacing: 0.2px;
    white-space: nowrap;
  }
  .holder__rule { flex: 1; height: 1px; background: var(--rule); }
  .holder__title { color: var(--ink); font-size: 12.5px; margin-top: -2px; }

  .address {
    position: absolute;
    left: 23px;
    top: 191px;
    color: var(--ink);
    font-size: 13px;
    line-height: 16px;
    font-style: normal;
  }
  .contacts {
    position: absolute;
    right: 28px;
    top: 153px;
    list-style: none;
    text-align: right;
    color: var(--ink);
    font-size: 13px;
    line-height: 16px;
  }
  .contacts li { display: flex; justify-content: flex-end; align-items: center; gap: 4px; white-space: nowrap; }
  .contacts svg { width: 9px; height: 9px; fill: var(--brand-blue); flex: none; }

  /* Back */
  .service {
    position: absolute;
    width: 140px;
    text-align: center;
    color: var(--ink);
    font-size: 9.5px;
    line-height: 12.5px;
    text-transform: uppercase;
  }
  .service__hex { display: block; margin: 0 auto 4px; width: 61px; height: 69px; }
  .service__hex polygon { fill: var(--brand-blue); }
</style>
</head>
<body>

<section class="card card--front">
  <div class="brand">
    <span class="brand__mark"></span>
    <span class="brand__name">BuildMark Solutions</span>
  </div>

  <div class="holder">
    <div class="holder__name-row">
      <span class="holder__name">DANA WHITFORD</span>
      <span class="holder__rule"></span>
    </div>
    <p class="holder__title">Managing Director</p>
  </div>

  <address class="address">
    48 Quarry Lane<br>
    Stonebridge, 204518
  </address>

  <ul class="contacts">
    <li>044-555 010 210
      <svg viewBox="0 0 10 10"><path d="M1 4 Q5 0 9 4 L8 5 L6.5 4 L6.5 3 Q5 2.5 3.5 3 L3.5 4 L2 5 Z M2.5 5.5 H7.5 L8 9 H2 Z"/></svg></li>
    <li>044-555 010 210
      <svg viewBox="0 0 10 10"><path d="M2.5 0 H7.5 V10 H2.5 Z M3.5 1 V8 H6.5 V1 Z" fill-rule="evenodd"/></svg></li>
    <li>info@buildmark-solutions.example
      <svg viewBox="0 0 10 10"><path d="M0 2 H10 V8 H0 Z M1 3 L5 6 L9 3 Z" fill-rule="evenodd"/></svg></li>
    <li>www.buildmark-solutions.example
      <svg viewBox="0 0 10 10"><circle cx="5" cy="5" r="4.8"/></svg></li>
  </ul>

  <div class="tagline-band">Measuring Needs - Delivering Results</div>
</section>

<section class="card card--back">
  <div class="service" style="left:16px; top:21px;">
    <svg class="service__hex" viewBox="0 0 60 69" role="img" aria-label="Project coordination icon"><polygon points="30,0 60,17 60,52 30,69 0,52 0,17"/></svg>
    Project Coordination<br>Management
  </div>
  <div class="service" style="left:152px; top:21px;">
    <svg class="service__hex" viewBox="0 0 60 69" role="img" aria-label="New software implementation icon"><polygon points="30,0 60,17 60,52 30,69 0,52 0,17"/></svg>
    New Software<br>Implementations
  </div>
  <div class="service" style="left:282px; top:21px;">
    <svg class="service__hex" viewBox="0 0 60 69" role="img" aria-label="Redesigning software usage icon"><polygon points="30,0 60,17 60,52 30,69 0,52 0,17"/></svg>
    Redesigning Software<br>Usage at the User Level
  </div>
  <div class="service" style="left:71px; top:123px;">
    <svg class="service__hex" viewBox="0 0 60 69" role="img" aria-label="Software re-implementation icon"><polygon points="30,0 60,17 60,52 30,69 0,52 0,17"/></svg>
    Software<br>Re-Implementations
  </div>
  <div class="service" style="left:218px; top:123px;">
    <svg class="service__hex" viewBox="0 0 60 69" role="img" aria-label="Continued software support icon"><polygon points="30,0 60,17 60,52 30,69 0,52 0,17"/></svg>
    Continued Software<br>Support
  </div>

  <div class="tagline-band">Measuring Needs - Delivering Results</div>
</section>

</body>
</html>
```